A Vegan Nutritional Supplement (one Product) website

I am looking for an experienced Web designer to build a One Product website for a Nutritional Supplement that is 100% vegan. The emphasis would be on both the Quality and Quantity of the ingredients and their benefits. It contains Essential Vitamins, Minerals, and a proprietary blend of 42 Fruits and Vegetables. I welcome color suggestions as long as it includes Green (vegan) and White.. The final design should communicate to the buyer: Quality, Healthy, Safety (Natural vegan ingredients), Natural energy, well being. The product includes benefits for 3 vital elements of optimal health: Immune Health, Heart Health, and Brain Health

Industry/Entity Type

Health and Wellness - Nutritional Supplements

Number of Pages Required

4 page

Other font styles liked:
• I Welcome your creativity

Colors
59FF00
82FF00
B8FF75
E3FFCB
F4FFEA

Requirements
Must have
• Options to purchase : One product ($34.95); 2 products ($31.45 each - 10% discount), or 3 Products ($27.95 each - 20% discount)
Nice to have
• Focus on the Benefits of having all these Ingredients - Nutrients in one bottle - Essential Vitamins, Minerals, and proprietary blend of 42 Fruits and Vegetables.

```html
<!DOCTYPE html>
<html lang="en">
<head>
<meta charset="utf-8">
<title>Leafwell Pure Vigor</title>
<link href="https://fonts.googleapis.com/css2?family=Michroma&family=Poppins:wght@400;500;600;700&display=swap" rel="stylesheet">
<style>
:root{
  --green-dark:#1e6f1c;
  --green:#3f9a25;
  --green-bright:#6cc13a;
  --green-label:#3d8b2b;
  --mint:#eefbe2;
  --mint-2:#f4ffea;
  --ink:#1d1d1d;
  --muted:#666;
  --line:#d9d9d9;
  --footer:#2b2b2b;
  --white:#fff;
}
*{box-sizing:border-box;margin:0;padding:0}
html,body{width:1200px;height:3988px;overflow:hidden;background:var(--white)}
body{position:relative;font-family:'Poppins',sans-serif;color:var(--ink)}
.abs{position:absolute}
.center{left:0;width:1200px;text-align:center}
.label{font-weight:600;letter-spacing:3px;color:var(--green-label);font-size:21px;line-height:1.2}
.heading{font-family:'Michroma',sans-serif;color:var(--ink);line-height:1.2;font-weight:400}
.btn{display:flex;align-items:center;justify-content:center;border-radius:30px;font-weight:600;font-size:12px;color:#fff;background:linear-gradient(90deg,var(--green-dark),var(--green-bright))}

/* header */
.site-header{top:0;left:0;width:1200px;height:132px;background:#fff}
.brand-badge{left:100px;top:6px;width:168px;height:168px;border-radius:50%;background:#fff;z-index:3}
.brand-badge .disc{position:absolute;left:10px;top:10px;width:148px;height:148px;border-radius:50%;background:radial-gradient(circle at 40% 35%,var(--green-bright),var(--green-dark));display:flex;flex-direction:column;align-items:center;justify-content:center;color:#fff;font-family:'Michroma',sans-serif;font-size:19px;line-height:1.15;text-align:center}
.brand-badge .disc small{font-size:12px;margin-bottom:4px}
.nav{top:86px;left:365px;display:flex;gap:37px;font-size:14px;font-weight:500}
.nav a{color:var(--ink);text-decoration:none}
.nav a.active{color:var(--green)}
.shop-btn{left:968px;top:75px;width:120px;height:42px;font-size:13px}
.search{left:766px;top:20px;width:230px;height:37px;border:2px solid #333;border-radius:20px}
/* hero */
.hero{top:132px;left:0;width:1200px;height:634px;background:linear-gradient(180deg,#5f8a3d 0%,#4d8b35 40%,#2f7a2a 80%,#2a7a2a 100%)}
.hero-runners{left:780px;top:150px;width:380px;height:580px;border-radius:40px;background:linear-gradient(180deg,rgba(230,170,80,.35),rgba(60,110,40,.1))}
.hero-small{top:190px;font-size:32px;line-height:1.2;letter-spacing:16px;color:#fff;font-family:'Michroma',sans-serif}
.hero-title{top:252px;font-size:56px;line-height:1.2;letter-spacing:10px;color:#fff;font-family:'Michroma',sans-serif;font-weight:400}
.bottles{left:380px;top:356px;width:440px;height:286px;border-radius:24px;background:linear-gradient(180deg,#f1f1ec 0%,#e6efd8 30%,#5a9a3a 55%,#2c6f2a 100%)}
.hero-buy{left:545px;top:690px;width:110px;height:38px;background:#fff;color:var(--green-dark);border-radius:20px;font-size:12px;font-weight:600;display:flex;align-items:center;justify-content:center}
/* ingredients */
.ingredients{top:766px;left:0;width:1200px;height:514px;background:var(--mint)}
.fruit-band{top:938px;left:0;width:1200px;height:342px;background:linear-gradient(90deg,#b33a2a,#e08a2a 20%,#7a2a4a 40%,#e8b63a 60%,#5a3a7a 80%,#8ab040)}
.ing-card{top:1019px;width:222px;height:168px;background:#fff;border-radius:6px;box-shadow:0 3px 10px rgba(0,0,0,.2);text-align:center;font-size:18px;font-weight:500;line-height:27px;padding-top:56px}
.ing-icon{width:94px;height:94px;border-radius:50%;background:#fff;border:3px solid #cfe9c2;display:flex;align-items:center;justify-content:center;top:970px}
/* about */
.about-img{left:593px;top:1378px;width:514px;height:449px}
.about p{font-size:14px;line-height:26px;color:var(--muted);text-align:justify}
/* order */
.order{top:1935px;left:0;width:1200px;height:678px;background:linear-gradient(90deg,#e6a94a 0%,#f7f7f4 18%,#fafafa 50%,#f7f7f4 82%,#8cc04a 100%)}
.order-tab{left:471px;top:1935px;width:258px;height:124px}
.order-card{left:111px;top:2099px;width:977px;height:436px;background:#fff;border:1px solid var(--line);box-shadow:0 2px 10px rgba(0,0,0,.12)}
.product-shot{left:186px;top:2028px;width:264px;height:472px;border-radius:40px 40px 30px 30px;background:linear-gradient(180deg,#f2f2f2 0 22%,#3b8a2a 22% 88%,#eaeaea 88%)}
.qty{left:623px;top:2250px;width:76px;height:36px;border:1px solid #aaa;border-radius:20px;display:flex;justify-content:space-around;align-items:center;font-size:14px}
/* benefits */
.benefit{top:2821px;width:307px;height:211px;border:2px solid var(--line);border-radius:4px;box-shadow:0 2px 8px rgba(0,0,0,.12);background:#fff;text-align:center}
.benefit .ico{margin:33px auto 0;width:98px;height:98px;border-radius:50%;background:linear-gradient(135deg,var(--green-bright),var(--green-dark));display:flex;align-items:center;justify-content:center}
.benefit h3{margin-top:28px;font-size:19px;font-weight:600;letter-spacing:2px}
/* testimonials */
.testimonials{top:3135px;left:0;width:1200px;height:472px;background:var(--mint)}
.t-card{top:3324px;width:406px;height:210px;background:#fff;border-radius:40px;box-shadow:0 4px 10px rgba(0,0,0,.12);padding:42px 26px 0 80px}
.t-card p{font-size:12.5px;line-height:23px;color:var(--muted);margin-top:10px}
.t-card h4{font-size:15px;font-weight:600;margin-top:12px}
.stars{color:#f0a020;font-size:11px;letter-spacing:1px}
.avatar{top:3373px;width:112px;height:112px;border-radius:50%;background:#fff;box-shadow:0 2px 8px rgba(0,0,0,.15)}
.avatar div{margin:10px;width:92px;height:92px;border-radius:50%;background:linear-gradient(180deg,#9aa0a6,#6a6e72)}
/* footer */
.footer{top:3607px;left:0;width:1200px;height:381px;background:var(--footer);color:#fff}
.f-col h5{font-size:16px;font-weight:600;margin-bottom:16px}
.f-col li{list-style:none;font-size:14px;line-height:39.5px;display:flex;align-items:center;gap:18px}
.f-col li::before{content:"";width:12px;height:12px;border-radius:50%;background:var(--green-bright)}
.social{top:3792px;width:38px;height:38px;border-radius:50%;background:#fff}
.social.first{background:var(--green-bright)}
.pay{top:3938px;width:38px;height:22px;border-radius:3px}
</style>
</head>
<body>

<header class="abs site-header">
  <div class="abs brand-badge"><div class="disc"><small>Leafwell</small>PURE<br>VIGOR</div></div>
  <div class="abs search"></div>
  <svg class="abs" style="left:780px;top:30px" width="18" height="18" viewBox="0 0 18 18"><circle cx="7" cy="7" r="5" fill="none" stroke="#222" stroke-width="2.4"/><line x1="11" y1="11" x2="15" y2="15" stroke="#222" stroke-width="2.4"/></svg>
  <svg class="abs" style="left:1023px;top:25px" width="22" height="26" viewBox="0 0 22 26"><circle cx="11" cy="8" r="6" fill="none" stroke="#333" stroke-width="2"/><path d="M2 25c0-6 4-9 9-9s9 3 9 9z" fill="none" stroke="#333" stroke-width="2"/></svg>
  <svg class="abs" style="left:1063px;top:25px" width="28" height="30" viewBox="0 0 28 30"><path d="M3 9h16l1 17H2z" fill="none" stroke="#333" stroke-width="2"/><path d="M7 9V6a4 4 0 0 1 8 0v3" fill="none" stroke="#333" stroke-width="2"/><circle cx="21" cy="24" r="5" fill="#3f9a25"/></svg>
  <nav class="abs nav">
    <a class="active">HOME</a><a>ABOUT US</a><a>OUR PRODUCTS</a><a>RESOURCES</a><a>CONTACT US</a>
  </nav>
  <div class="abs btn shop-btn">SHOP NOW</div>
</header>

<section class="abs hero" role="img" aria-label="Couple jogging through a sunny green park"></section>
<div class="abs hero-runners" role="img" aria-label="Runners in sportswear"></div>
<div class="abs center hero-small">LEAFWELL</div>
<h1 class="abs center hero-title">PURE VIGOR</h1>
<div class="abs bottles" role="img" aria-label="Three supplement bottles with green labels"></div>
<div class="abs hero-buy">BUY NOW</div>

<section class="abs ingredients"></section>
<div class="abs fruit-band" role="img" aria-label="Assorted fresh fruits and berries"></div>
<div class="abs center label" style="top:850px">OUR INGREDIENTS</div>
<h2 class="abs center heading" style="top:888px;font-size:34px;line-height:40px;letter-spacing:3px">PURE VIGOR</h2>

<div class="abs ing-card" style="left:111px">Nutrients in one<br>bottle</div>
<div class="abs ing-card" style="left:363px">Essential Vitamins</div>
<div class="abs ing-card" style="left:615px">Minerals</div>
<div class="abs ing-card" style="left:866px">proprietary blend of<br>42 Fruits and<br>Vegetables</div>
<div class="abs ing-icon" style="left:175px"><svg width="44" height="44" viewBox="0 0 44 44" fill="none" stroke="#3f9a25" stroke-width="2"><rect x="12" y="6" width="20" height="6" rx="2"/><rect x="9" y="12" width="26" height="26" rx="4"/><circle cx="22" cy="25" r="6"/></svg></div>
<div class="abs ing-icon" style="left:427px"><svg width="44" height="44" viewBox="0 0 44 44" fill="none" stroke="#3f9a25" stroke-width="2"><circle cx="16" cy="26" r="10"/><circle cx="30" cy="18" r="7"/><path d="M30 11l4-6"/></svg></div>
<div class="abs ing-icon" style="left:679px"><svg width="44" height="44" viewBox="0 0 44 44" fill="none" stroke="#3f9a25" stroke-width="2"><path d="M22 6c6 9 9 13 9 18a9 9 0 0 1-18 0c0-5 3-9 9-18z"/><path d="M8 36h28"/></svg></div>
<div class="abs ing-icon" style="left:930px"><svg width="44" height="44" viewBox="0 0 44 44" fill="none" stroke="#3f9a25" stroke-width="2"><path d="M6 22h32a16 16 0 0 1-32 0z"/><circle cx="16" cy="15" r="5"/><circle cx="28" cy="15" r="5"/><path d="M22 6v6"/></svg></div>

<section class="abs about" style="left:111px;top:1420px;width:440px">
  <div class="label" style="font-size:16px">PURE VIGOR</div>
  <h2 class="heading" style="font-size:18.5px;line-height:34px;margin-top:18px;white-space:nowrap">A POWERFUL SUPPLEMENT FOR<br>GETTING OPTIMAL HEALTH</h2>
  <p style="margin-top:22px">When healthy food is a nuisance, a weak immune system, the risk of chronic and mental illnesses in old age is quite common. According to one report of NHRA, the majority of the US population is not able to get the necessary nutrients by a healthy diet alone1. Therefore, you must take supplements to meet your nutrient needs.</p>
  <div class="btn" style="margin-top:38px;width:129px;height:41px">READ MORE</div>
</section>
<svg class="abs about-img" viewBox="0 0 514 449">
  <path d="M330 2a222 222 0 0 1 0 445" fill="none" stroke="#5fb030" stroke-width="6"/>
  <circle cx="320" cy="224" r="212" fill="#6a86b0"/>
</svg>
<div class="abs" style="left:850px;top:1400px;width:260px;height:400px;border-radius:0 200px 200px 0" role="img" aria-label="Hiker on a mountain peak at sunrise"></div>
<div class="abs" style="left:593px;top:1378px;width:250px;height:449px;border-radius:40px 40px 30px 30px;background:linear-gradient(180deg,#f2f2f2 0 22%,#3b8a2a 22% 90%,#eaeaea 90%)" role="img" aria-label="Supplement bottle with green label"></div>

<section class="abs order" role="img" aria-label="Fresh fruit and vegetables framing the section"></section>
<svg class="abs order-tab" viewBox="0 0 258 124"><defs><linearGradient id="tab" x1="0" x2="1"><stop offset="0" stop-color="#1e6f1c"/><stop offset="1" stop-color="#6cc13a"/></linearGradient></defs><path d="M0 0h258v62L129 124 0 62z" fill="url(#tab)"/><text x="129" y="50" text-anchor="middle" font-family="Michroma,sans-serif" font-size="23" fill="#fff">ORDER NOW</text></svg>
<div class="abs order-card"></div>
<div class="abs product-shot" role="img" aria-label="Supplement bottle with green label"></div>
<div class="abs label" style="left:522px;top:2164px;font-size:16px">OPTIONS TO PURCHASE</div>
<h2 class="abs heading" style="left:522px;top:2198px;font-size:24px">LEAFWELL PURE VIGOR</h2>
<div class="abs" style="left:522px;top:2258px;font-size:13px;letter-spacing:2px;color:#555">QUANTITY</div>
<div class="abs qty"><span>–</span><span>2</span><span>+</span></div>
<div class="abs btn" style="left:706px;top:2251px;width:93px;height:35px;font-size:10px">BUY NOW</div>
<div class="abs" style="left:522px;top:2304px;font-size:13px;font-weight:600;color:var(--green)"><s style="color:#999">$34.95</s>&nbsp; $31.45 EACH - 10% DISCOUNT</div>
<p class="abs" style="left:522px;top:2338px;width:490px;font-size:14px;line-height:26px;color:var(--muted);text-align:justify">Pure Vigor is a supplement that you must take daily to improve your overall health, increase longevity, and enhance life quality. Children under 18, individuals with a known medical condition, and pregnant or nursing mothers should consult a physician before using this dietary supplement.</p>

<div class="abs center label" style="top:2700px">OUR BENEFITS</div>
<h2 class="abs center heading" style="top:2744px;font-size:25px;letter-spacing:1px">VITAL ELEMENTS OF OPTIMAL HEALTH</h2>
<div class="abs benefit" style="left:111px"><div class="ico"><svg width="50" height="50" viewBox="0 0 50 50" fill="none" stroke="#fff" stroke-width="2.4"><path d="M25 6l15 6v12c0 10-7 17-15 20-8-3-15-10-15-20V12z"/><path d="M25 17v14M18 24h14"/></svg></div><h3>IMMUNE HEALTH</h3></div>
<div class="abs benefit" style="left:446px"><div class="ico"><svg width="50" height="50" viewBox="0 0 50 50" fill="none" stroke="#fff" stroke-width="2.4"><path d="M25 42S7 31 7 18a9 9 0 0 1 18-3 9 9 0 0 1 18 3c0 13-18 24-18 24z"/><path d="M10 26h9l3-6 4 10 3-4h11"/></svg></div><h3>HEART HEALTH</h3></div>
<div class="abs benefit" style="left:780px"><div class="ico"><svg width="50" height="50" viewBox="0 0 50 50" fill="none" stroke="#fff" stroke-width="2.4"><path d="M24 8c-7 0-11 4-11 9-5 2-6 9-2 12-1 6 4 10 10 9h3zM26 8c7 0 11 4 11 9 5 2 6 9 2 12 1 6-4 10-10 9h-3z"/></svg></div><h3>BRAIN HEALTH</h3></div>

<section class="abs testimonials"></section>
<div class="abs center label" style="top:3206px">TESTIMONIALS</div>
<h2 class="abs center heading" style="top:3248px;font-size:27px;letter-spacing:2px">WHAT OUR CLIENTS SAY</h2>

<div class="abs t-card" style="left:182px">
  <svg width="26" height="20" viewBox="0 0 26 20" fill="#3f9a25"><path d="M0 10C0 4 3 1 9 0v4c-3 1-4 3-4 5h5v11H0zM14 10c0-6 3-9 9-10v4c-3 1-4 3-4 5h5v11H14z"/></svg>
  <p>Lorem ipsum dolor sit amet, consectetur adipiscing elit, sed do eiusmod tempor incididunt ut labore et dolore magna aliq enim ad minimea.</p>
  <h4>SAM CARTER</h4><div class="stars">★★★★★</div>
</div>
<div class="abs avatar" style="left:130px" role="img" aria-label="Customer portrait"><div></div></div>
<div class="abs t-card" style="left:665px">
  <svg width="26" height="20" viewBox="0 0 26 20" fill="#3f9a25"><path d="M0 10C0 4 3 1 9 0v4c-3 1-4 3-4 5h5v11H0zM14 10c0-6 3-9 9-10v4c-3 1-4 3-4 5h5v11H14z"/></svg>
  <p>Lorem ipsum dolor sit amet, consectetur adipiscing elit, sed do eiusmod tempor incididunt ut labore et dolore magna aliq enim ad minimea.</p>
  <h4>SAM CARTER</h4><div class="stars">★★★★★</div>
</div>
<div class="abs avatar" style="left:613px" role="img" aria-label="Customer portrait"><div></div></div>

<footer class="abs footer"></footer>
<div class="abs" style="left:111px;top:3700px;color:#fff;font-family:'Michroma',sans-serif;text-align:center;width:195px">
  <div style="font-size:17px">Leafwell</div>
  <div style="font-size:32px;line-height:42px;margin-top:16px">PURE<br>VIGOR</div>
</div>
<div class="abs f-col" style="left:359px;top:3672px;color:#fff"><h5>LET US HELP YOU</h5><ul><li>Home</li><li>About Us</li><li>Our Products</li><li>Resources</li><li>Contact Us</li></ul></div>
<div class="abs f-col" style="left:573px;top:3672px;color:#fff"><h5>QUICK LINKS</h5><ul><li>Shipping</li><li>Privacy Policy</li><li>Terms Of Use</li><li>Customer Services</li><li>Disclaimer</li></ul></div>
<div class="abs" style="left:805px;top:3672px;color:#fff;font-size:16px;font-weight:600">NEWSLETTER SIGNUP</div>
<div class="abs" style="left:805px;top:3720px;width:283px;height:48px;background:#fff;border-radius:26px;font-size:14px;color:#555;padding:13px 16px">Email Address</div>
<div class="abs btn" style="left:981px;top:3724px;width:103px;height:40px;font-size:13px">SIGN UP</div>
<div class="abs social first" style="left:805px"></div>
<div class="abs social" style="left:848px"></div>
<div class="abs social" style="left:891px"></div>
<div class="abs" style="left:111px;top:3928px;width:977px;height:1px;background:#555"></div>
<div class="abs center" style="top:3943px;font-size:12.5px;color:#fff">© 2022 Leafwell PURE VIGOR &nbsp;|&nbsp; All Rights Reserved</div>
<div class="abs pay" style="left:881px;background:#eee"></div>
<div class="abs pay" style="left:924px;background:#2a4a9a"></div>
<div class="abs pay" style="left:967px;background:#e8e8e8"></div>
<div class="abs pay" style="left:1009px;background:#3a7ac8"></div>
<div class="abs pay" style="left:1051px;background:#ddd"></div>

</body>
</html>
```